Business Card Design

We would like to re-design our business cards. Our Company - Qwinrel Turbochargers, rebuilds turbochargers and sells replacement parts. Our website is: http://www.qwinrelturbochargers-example.com
We just had our logo changed. I will attach the file. Looking for fresh new/modern business card. We like the colors red, black, white and silver. Black background looks attractive, but not a requirement. The final design should communicate reasonable/competitive prices, top quality and reliability of our products.
Updates
Project Deadline Extended
Reason: Need to finalize the info on the card. Currently working on changing address and email info. Want to make sure it is the correct one before accepting the final design. Unless, this is something that can be changed at a later time..??
Industry/Entity Type
Business
Contact Information for Business Card
QWINREL TURBOCHARGERS, LLC
20473 Harwick Lane NE
Massillon, OH 44647
Tel: +1-555-214-7390
Fax: +1-555-267-1842
info@QwinrelTurbochargers-example.com
Our current business card had the following highlights:
*We rebuild all Turbocharges for Automotive, Diesel and Industrial
*Precision Balancing and in-house turbocharger needs
*All Turbocharger replacement parts are made in USA / U.K.
Look and feel
Each slider illustrates characteristics of the customer's brand and the style your logo design should communicate.

```html
<!DOCTYPE html>
<html lang="en">
<head>
<meta charset="utf-8">
<title>Qwinrel Turbochargers – Business Card</title>
<link rel="stylesheet" href="https://fonts.googleapis.com/css2?family=Montserrat:wght@400;500;700;800&display=swap">
<style>
  :root {
    --backdrop: #d9d9d9;
    --card: #ffffff;
    --ink: #1a1a1a;
    --ink-soft: #333333;
    --red: #e0221b;
    --black: #111111;
    --faint: #f1f1f1;
  }
  * { box-sizing: border-box; margin: 0; padding: 0; }
  html, body { width: 1200px; height: 852px; overflow: hidden; }
  body {
    background: var(--backdrop);
    font-family: "Montserrat", sans-serif;
    color: var(--ink);
    position: relative;
  }
  .card {
    position: absolute;
    top: 276px;
    width: 525px;
    height: 300px;
    background: var(--card);
    border-radius: 22px;
    overflow: hidden;
  }
  .card--front { left: 50px; }
  .card--back  { left: 625px; }

  .brand {
    display: flex;
    align-items: center;
    gap: 10px;
    font-weight: 800;
    color: var(--ink);
    line-height: 1;
    white-space: nowrap;
  }
  .brand__mark { width: 18px; height: 18px; background: var(--red); flex: none; }

  .faint-art {
    position: absolute;
    border-radius: 50%;
    background: radial-gradient(circle, var(--faint) 0%, rgba(241,241,241,0) 70%);
  }

  /* front */
  .card--front .faint-art { right: -40px; top: -60px; width: 320px; height: 320px; }
  .card--front .brand { position: absolute; left: 50%; top: 112px; transform: translateX(-50%); font-size: 27px; }
  .card--front .brand__mark { width: 24px; height: 24px; }
  .front__rule { position: absolute; height: 2px; background: var(--red); }
  .front__rule--top { right: 30px; top: 94px; width: 70px; }
  .front__rule--bottom { left: 30px; top: 232px; width: 70px; }
  .front__url {
    position: absolute; left: 50%; top: 186px; transform: translateX(-50%);
    font-size: 13px; font-weight: 500; color: var(--ink-soft); white-space: nowrap;
  }

  /* back */
  .card--back .faint-art { right: 20px; top: 20px; width: 200px; height: 200px; }
  .card--back .brand { position: absolute; left: 52px; top: 58px; font-size: 21px; }
  .person { position: absolute; left: 34px; top: 196px; text-align: right; }
  .person__name { font-size: 16px; font-weight: 700; color: var(--red); }
  .person__title { font-size: 12px; color: var(--ink-soft); margin-top: 2px; }
  .divider { position: absolute; left: 228px; top: 132px; width: 1px; height: 112px; background: var(--red); opacity: .6; }
  .contact { position: absolute; left: 244px; top: 138px; list-style: none; font-size: 11.5px; color: var(--ink-soft); line-height: 1.55; }
  .contact li { display: flex; align-items: center; gap: 7px; }
  .contact svg { width: 10px; height: 10px; fill: var(--red); flex: none; }
  .contact .contact__address { padding-left: 0; }
  .swoosh { position: absolute; right: 0; bottom: 0; width: 525px; height: 300px; }
</style>
</head>
<body>
  <section class="card card--front" aria-label="Card front">
    <div class="faint-art" role="img" aria-label="Faint turbocharger decoration"></div>
    <span class="front__rule front__rule--top"></span>
    <div class="brand"><span class="brand__mark"></span>Qwinrel Turbochargers</div>
    <p class="front__url">www.QwinrelTurbochargers-example.com</p>
    <span class="front__rule front__rule--bottom"></span>
  </section>

  <section class="card card--back" aria-label="Card back">
    <div class="faint-art" role="img" aria-label="Faint turbocharger decoration"></div>
    <div class="brand"><span class="brand__mark"></span>Qwinrel Turbochargers</div>
    <div class="person">
      <p class="person__name">Your Long Name</p>
      <p class="person__title">Title</p>
    </div>
    <span class="divider"></span>
    <ul class="contact">
      <li><svg viewBox="0 0 10 10"><path d="M2 0h2l1 3-1.5 1a6 6 0 0 0 2.5 2.5L7 5l3 1v2c0 1-1 2-2 2A8 8 0 0 1 0 2c0-1 1-2 2-2z"/></svg>1.555.214.7390</li>
      <li><svg viewBox="0 0 10 10"><path d="M0 2h10v6H0z M0 2l5 3.5L10 2" stroke="#fff" stroke-width=".8"/></svg>info@QwinrelTurbochargers-example.com</li>
      <li><svg viewBox="0 0 10 10"><circle cx="5" cy="5" r="5"/></svg>www.QwinrelTurbochargers-example.com</li>
      <li class="contact__address">4718 Brindle Ave. NW</li>
      <li class="contact__address">Corvale, Ohio</li>
    </ul>
    <svg class="swoosh" viewBox="0 0 525 300" aria-hidden="true">
      <path d="M300 300 C330 272 350 262 390 258 L525 250 L525 300 Z" fill="var(--black)"/>
      <path d="M390 258 C420 240 440 236 470 234 L525 228 L525 250 Z" fill="var(--red)"/>
    </svg>
  </section>
</body>
</html>
```